KDWB Business Card

Looking for a business card design to incorporate our branding. We want to only use the colors listing in the Branding Package (attached).
Updates

Target Market(s)

People who need their phone or device fixed.

Industry/Entity Type

Electronics

Contact Information for Business Card

Please use:

Brightwick Gadget Clinic LLC
4810 E Harlow Ridge Rd
Suite 417
San Antonio, TX 78163

Marcus Delgrove, Store Manager

(210) 555-0147

Requirements
Must have
• Must include the colors that are contained within the Branding Package PDF file.

```html
<!DOCTYPE html>
<html lang="en">
<head>
<meta charset="utf-8">
<title>Brightwick Gadget Clinic – Business Card</title>
<link href="https://fonts.googleapis.com/css2?family=Arimo:wght@400;700&display=swap" rel="stylesheet">
<style>
  :root {
    --brand-orange: #f26b2a;
    --brand-grey: #6d6e71;
    --ink: #2e2e2e;
    --paper: #ffffff;
    --backdrop: #e9e6e1;
  }
  * { box-sizing: border-box; margin: 0; padding: 0; }
  html, body { width: 1200px; height: 901px; overflow: hidden; }
  body {
    background: var(--backdrop);
    font-family: "Arimo", Arial, sans-serif;
    display: flex;
    flex-direction: column;
    align-items: center;
    justify-content: center;
    gap: 40px;
  }
  .card {
    width: 640px;
    height: 366px;
    background: var(--paper);
    position: relative;
    box-shadow: 0 6px 18px rgba(0,0,0,0.18);
    overflow: hidden;
  }
  /* Brand lockup */
  .brand {
    display: flex;
    align-items: center;
    gap: 12px;
    color: var(--brand-orange);
    font-weight: 400;
    white-space: nowrap;
  }
  .brand-mark {
    display: block;
    background: var(--brand-orange);
    border-radius: 6px;
  }
  /* Back side */
  .card-back .brand {
    position: absolute;
    left: 50%; top: 50%;
    transform: translate(-50%, -50%);
    font-size: 34px;
  }
  .card-back .brand-mark { width: 40px; height: 40px; }
  /* Front side */
  .card-front .brand {
    position: absolute;
    right: 40px; top: 44px;
    font-size: 28px;
  }
  .card-front .brand-mark { width: 32px; height: 32px; }
  .person {
    position: absolute;
    left: 40px; top: 150px;
  }
  .person-name {
    font-size: 24px;
    color: var(--ink);
    letter-spacing: 0.2px;
  }
  .person-title {
    font-size: 13px;
    color: var(--brand-orange);
    margin-top: 4px;
  }
  .divider {
    position: absolute;
    left: 300px; top: 140px;
    width: 1.5px; height: 92px;
    background: var(--ink);
  }
  .contacts {
    position: absolute;
    left: 324px; top: 146px;
    list-style: none;
    font-size: 15px;
    color: var(--ink);
  }
  .contacts li {
    display: flex;
    align-items: center;
    gap: 10px;
    margin-bottom: 9px;
  }
  .contact-icon { width: 16px; height: 16px; flex: none; }
  .address-band {
    position: absolute;
    left: 0; right: 0; bottom: 0;
    height: 58px;
    background: var(--brand-grey);
    color: var(--paper);
    font-size: 17px;
    display: flex;
    align-items: center;
    padding-left: 40px;
    letter-spacing: 0.3px;
  }
</style>
</head>
<body>

  <section class="card card-back" aria-label="Card back">
    <div class="brand">
      <span class="brand-mark"></span>
      <span class="brand-name">Brightwick Gadget Clinic</span>
    </div>
  </section>

  <section class="card card-front" aria-label="Card front">
    <div class="brand">
      <span class="brand-mark"></span>
      <span class="brand-name">Brightwick Gadget Clinic</span>
    </div>

    <div class="person">
      <p class="person-name">Marcus Delgrove</p>
      <p class="person-title">Store Manager</p>
    </div>

    <div class="divider"></div>

    <ul class="contacts">
      <li>
        <svg class="contact-icon" viewBox="0 0 16 16" aria-hidden="true">
          <rect width="16" height="16" rx="2" fill="var(--brand-orange)"/>
          <path d="M5 3.5 L6.8 3.5 L7.4 6 L6.3 6.8 Q7.3 9 9.2 9.8 L10 8.7 L12.5 9.3 L12.5 11 Q12 12.5 10.5 12.4 Q4 11.5 3.6 5 Q3.6 3.6 5 3.5Z" fill="#fff"/>
        </svg>
        <span>(210) 555-0147</span>
      </li>
      <li>
        <svg class="contact-icon" viewBox="0 0 16 16" aria-hidden="true">
          <rect width="16" height="16" rx="2" fill="var(--brand-orange)"/>
          <rect x="3" y="4.5" width="10" height="7" fill="none" stroke="#fff" stroke-width="1.3"/>
          <path d="M3 4.5 L8 8.6 L13 4.5" fill="none" stroke="#fff" stroke-width="1.3"/>
        </svg>
        <span>marcus@BrightwickClinic.com</span>
      </li>
      <li>
        <svg class="contact-icon" viewBox="0 0 16 16" aria-hidden="true">
          <rect width="16" height="16" rx="2" fill="var(--brand-orange)"/>
          <circle cx="8" cy="8" r="4.6" fill="none" stroke="#fff" stroke-width="1.2"/>
          <ellipse cx="8" cy="8" rx="2" ry="4.6" fill="none" stroke="#fff" stroke-width="1"/>
          <line x1="3.4" y1="8" x2="12.6" y2="8" stroke="#fff" stroke-width="1"/>
        </svg>
        <span>www.BrightwickClinic.com</span>
      </li>
    </ul>

    <div class="address-band">4810 E Harlow Ridge Rd, Suite 417, San Antonio, TX 78163</div>
  </section>

</body>
</html>
```